VocaTerrana Community/ Talent Gallery

VocaTerrana is developing a collaborative career course, with coaching and community exchange. Goal is to offer a platform where talented candidates can show their expertise and find projects, partners, and develop their online portfolios!

Here is a good example of the type of thing we hope to create with focus on sustainability focused talent to task matching
http://www.brambleforth.com/global-themes/employment-and-growth/connecting-talent-with-opportunity-in-the-digital-age

We hope to have a "grid style" gallery where it is easy to search by talent types and focus areas within the scope of "Sustainability" issues...Food/Water/Energy, Public Health, Technology, Sustainable Cities, Infrastructure, Education, Policy, Emerging Economies, Ecosystems, Social Innovation, inclusive Security, Equity Issues. For each topic/ header we hope to have candidates post their completed portfolios to exhibit resumes, biography, a case study... they may actually prepare these on other sites, but can link in OR alternately that they can easily create here, similar to "pinqo.io" ....

Hope to include a blog space titled "Rising over the Rift", where people can mix it up across these topic issues as they are interdependent and often require partners across discipline areas! If possible another area where jobs related to these issues may be posted as project or job opportunities by potential employers.

If there is a way to create a feed from various job sites that already exist...like Jobora...or http://www.greenledgerworks.com/ that would be super great. Again...sort of a portal connection to bridge the gap ....instead of candidates having to search all the time, we are hoping they can advertise their talent and employers may search here for these well presented portfolios!

Target Market(s)

Educators, Students, Career Transitioners, Employers, Professional Associations, Talent Recruiters with focus on Sustainability related Talent to Task matching!

Industry/Entity Type

Sustainability

Number of Pages Required

4 page

Font styles to use
Sans Serif

Colors
3176b5
32b8a4
add136

Requirements
Must have
• Not sure about the coded/ uncoded option here....
• Must have - grid style area where Sustainability Professionals with varied focus areas can exhibit their talent portfolios
• appear as a Talent Gallery that starts with photos & obvious organization...other tabs to be in a menu.
• ability to search both talent and task opportunity areas to help coaches or community members make matches....some topic focused category or tag words to help make them searchable...???
• consistent professional styling to existing website and new artflock postcard shared in brief/ images area
• Interactive blog space where articles, issues may be posted, discussed
• Bulletin board or feed for project opportunities to be posted where candidates may locate them and/or employers may express specific "call" for talent..These may be Short term Internships, Projects, Consulting Team Opportunity, or Jobs/ part time to full time....
Nice to have
• A calendar area where we can post networking opportunities, issues presentations where potential partners can meet the next generation leaders, attend a forum or webinar presentation.
Should not have
• Too much text on front page...Should be clean design,

```html
<!DOCTYPE html>
<html lang="en">
<head>
<meta charset="utf-8">
<title>VocaTerrana – Career Collaboration for a Sustainable Future</title>
<link href="https://fonts.googleapis.com/css2?family=Open+Sans:ital,wght@0,400;0,600;0,700;1,400;1,600&display=swap" rel="stylesheet">
<style>
:root{
  --blue:#3176b5;
  --teal:#32b8a4;
  --lime:#add136;
  --navy:#23558f;
  --ink:#2b2b2b;
  --text:#444;
  --muted:#777;
  --dark:#333333;
  --footer:#2c2c2c;
  --light:#f3f3f3;
  --white:#fff;
}
*{box-sizing:border-box;margin:0;padding:0}
html,body{width:1200px;height:4082px;overflow:hidden;background:var(--white)}
body{font-family:"Open Sans",Arial,sans-serif;color:var(--text)}
.page{position:relative;width:1200px;height:4082px;overflow:hidden}
.abs{position:absolute}
.photo{position:absolute}
.hl{color:var(--blue)}

/* header */
.site-header{position:absolute;left:0;top:0;width:1200px;height:114px;background:var(--white)}
.brand{position:absolute;left:109px;top:44px;display:flex;align-items:center;gap:14px;font-size:40px;font-weight:600;color:var(--ink);letter-spacing:-.5px}
.brand-dot{width:56px;height:56px;border-radius:50%;background:var(--teal)}
.login{position:absolute;left:822px;top:16px;width:86px;height:34px;border:2px solid #cfcfcf;border-radius:17px;font-size:12px;font-weight:700;color:var(--ink);display:flex;align-items:center;justify-content:center;gap:6px}
.phone-top{position:absolute;left:932px;top:14px;display:flex;align-items:center;gap:12px;font-size:21px;color:var(--ink)}
.phone-top .ic{width:34px;height:34px;border-radius:50%;background:var(--navy);display:flex;align-items:center;justify-content:center}
.main-nav{position:absolute;top:64px;left:0;width:1200px}
.main-nav a{position:absolute;font-size:16px;color:var(--ink);text-decoration:none;height:36px;line-height:36px;letter-spacing:.5px}
.main-nav a.active{background:var(--teal);color:var(--white);border-radius:18px;padding:0 22px}

/* hero */
.hero{position:absolute;left:0;top:114px;width:1200px;height:534px;background:radial-gradient(ellipse at 50% 45%,#5aa8d8 0%,#9fcde6 30%,#c7b49b 52%,#e7ddd2 75%,#f3f0ec 100%)}
.hero-arrow{position:absolute;top:230px}
.hero-caption{position:absolute;left:0;bottom:0;width:1200px;height:54px;background:rgba(40,40,40,.55)}
.hero-caption p{position:absolute;left:99px;top:11px;font-size:25px;font-style:italic;font-weight:600;color:var(--white)}
.pill{display:flex;align-items:center;justify-content:space-between;background:var(--navy);color:var(--white);border-radius:20px;font-size:14px;padding:0 4px 0 18px}
.pill .go{width:28px;height:28px;border-radius:50%;background:var(--white);display:flex;align-items:center;justify-content:center}
.hero-caption .pill{position:absolute;left:962px;top:10px;width:128px;height:36px}

/* section titles */
.sec-title{position:absolute;left:0;width:1200px;text-align:center;font-size:36px;color:var(--ink);font-weight:400}
.divider{position:absolute;left:360px;width:480px;height:40px}
.divider:before{content:"";position:absolute;left:0;right:0;top:19px;height:2px;background:#d4d4d4}
.divider:after{content:"";position:absolute;left:222px;top:2px;width:36px;height:36px;border-radius:50%;background:var(--teal);box-shadow:0 0 0 10px var(--white)}
.lead{position:absolute;text-align:center;color:var(--ink)}

/* welcome */
.feature{position:absolute;display:flex;gap:22px}
.feature .ic{width:58px;height:58px;border-radius:50%;border:2px solid #ddd;display:flex;align-items:center;justify-content:center;flex:none}
.feature h3{font-size:17px;font-weight:700;color:var(--navy)}
.feature h3 span{color:var(--blue);font-weight:700}
.feature p{font-size:12px;line-height:16px;color:var(--ink);width:300px}
.feature p em{font-style:normal;color:var(--blue)}

.service-band{position:absolute;left:0;top:1045px;width:1200px;height:283px;background:var(--dark)}
.service{position:absolute;top:985px;width:236px;text-align:center}
.service .photo{position:relative;width:236px;height:186px;border:4px solid var(--teal)}
.service .badge{position:absolute;left:94px;top:150px;width:48px;height:48px;border-radius:50%;background:var(--teal);border:3px solid var(--white)}
.service h4{margin-top:26px;font-size:23px;font-weight:400;color:var(--white);line-height:30px;letter-spacing:.5px}
.service .pill{position:absolute;left:54px;top:296px;width:130px;height:36px}

/* four phases */
.phases{position:absolute;left:0;top:1328px;width:1200px;height:767px;background:linear-gradient(160deg,#ffffff 0%,#f1f1f1 40%,#e9e9e9 70%,#f4f4f4 100%)}
.phase{position:absolute;width:300px;text-align:center}
.phase h5{font-size:20px;font-weight:700;color:var(--ink)}
.phase p{font-size:15px;line-height:22px;color:var(--text);margin-top:6px}
.phase .dot{width:26px;height:26px;border-radius:50%;margin:12px auto 0;display:flex;align-items:center;justify-content:center}

/* coaches */
.coach-photo{position:absolute;width:214px;height:214px;border-radius:50%}
.coach{position:absolute;width:270px}
.coach h6{font-size:16px;font-weight:400;color:var(--ink)}
.coach p{font-size:11.5px;line-height:17px;color:var(--text);margin-top:12px}
.coach a{display:block;margin-top:6px;font-size:12px;font-weight:700;color:var(--ink);text-decoration:none}

/* gallery */
.gallery-bg{position:absolute;left:0;top:2517px;width:1200px;height:716px;background:var(--white)}
.tile{position:absolute;overflow:hidden}
.tile span{position:absolute;left:0;right:0;bottom:0;height:54px;line-height:54px;background:rgba(0,0,0,.35);color:var(--white);font-size:29px;text-align:center}
.tile span.top{bottom:auto;top:26px;background:none}

/* blog */
.blog-bg{position:absolute;left:0;top:3233px;width:1200px;height:495px;background:var(--light)}
.post{position:absolute;top:3396px;width:313px}
.post .photo{position:relative;width:313px;height:148px}
.post .date{position:absolute;left:0;top:0;width:46px;height:48px;background:var(--blue);color:var(--white);text-align:center;font-size:18px;font-weight:700;line-height:22px;padding-top:3px}
.post .date small{display:block;font-size:11px;line-height:14px}
.post h4{margin-top:16px;font-size:15px;font-weight:700;color:var(--ink)}
.post p{margin-top:4px;font-size:12.5px;line-height:17px;color:var(--text)}
.post a{display:block;margin-top:10px;font-size:13px;font-weight:700;color:var(--blue);text-decoration:none}
.side-arrow{position:absolute;top:3476px}

/* footer */
.site-footer{position:absolute;left:0;top:3728px;width:1200px;height:310px;background:var(--footer)}
.footer-curve{position:absolute;left:0;top:3700px;width:1200px;height:60px}
.footer-badge{position:absolute;left:571px;top:3690px;width:58px;height:58px;border-radius:50%;background:var(--white)}
.footer-badge:after{content:"";position:absolute;left:13px;top:13px;width:32px;height:32px;border-radius:50%;background:var(--teal)}
.fcol{position:absolute;top:3790px;color:#ddd;font-size:13px}
.fcol h5{font-size:20px;font-weight:400;color:var(--teal);margin-bottom:18px}
.fcol ul{list-style:none}
.fcol li{line-height:27px}
.fcol li:before{content:"•";margin-right:6px}
.fcol .line{display:flex;align-items:center;gap:8px;margin-top:10px}
.field{width:255px;height:29px;background:var(--white);margin-bottom:10px;color:#999;font-size:11px;padding:6px 10px}
.field.msg{height:40px}
.submit{width:118px;height:30px;background:var(--blue);color:var(--white);font-size:13px;font-weight:700;line-height:30px;text-align:center}
.feed-head{font-size:13px;color:var(--white);margin-bottom:14px}
.feed-head small{font-size:9px;color:var(--teal);margin-left:12px}
.feed li{line-height:16px;margin-bottom:14px;font-size:12.5px}
.feed li small{display:block;padding-left:12px;font-size:11px;color:#bbb}
.copyright{position:absolute;left:0;top:4038px;width:1200px;height:44px;background:var(--blue);color:var(--white);font-size:13px;text-align:center;line-height:44px;font-weight:600}
</style>
</head>
<body>
<div class="page">

<header class="site-header">
  <div class="brand"><span class="brand-dot"></span>VocaTerrana</div>
  <div class="login">
    <svg width="10" height="12" viewBox="0 0 10 12"><rect x="1" y="5" width="8" height="7" rx="1" fill="#2b2b2b"/><path d="M3 5V3a2 2 0 0 1 4 0v2" stroke="#2b2b2b" stroke-width="1.5" fill="none"/></svg>LOGIN
  </div>
  <div class="phone-top">
    <span class="ic"><svg width="16" height="16" viewBox="0 0 24 24"><path fill="#fff" d="M6.6 10.8a15 15 0 0 0 6.6 6.6l2.2-2.2a1 1 0 0 1 1-.25 11.4 11.4 0 0 0 3.6.6 1 1 0 0 1 1 1V20a1 1 0 0 1-1 1A17 17 0 0 1 3 4a1 1 0 0 1 1-1h3.5a1 1 0 0 1 1 1c0 1.25.2 2.45.6 3.6a1 1 0 0 1-.25 1z"/></svg></span>
    555-014-2390
  </div>
  <nav class="main-nav">
    <a class="active" style="left:571px">HOME</a>
    <a style="left:708px">ABOUT</a>
    <a style="left:808px">SERVICES</a>
    <a style="left:930px">BLOG</a>
    <a style="left:1024px">CONTACT</a>
  </nav>
</header>

<section class="hero" role="img" aria-label="Hands of several people forming a circle around a globe of the Earth">
  <svg class="hero-arrow" style="left:40px" width="30" height="60" viewBox="0 0 30 60"><path d="M26 4 4 30l22 26" stroke="#fff" stroke-width="3" fill="none"/></svg>
  <svg class="hero-arrow" style="left:1130px" width="30" height="60" viewBox="0 0 30 60"><path d="M4 4l22 26L4 56" stroke="#fff" stroke-width="3" fill="none"/></svg>
  <div class="hero-caption">
    <p>Career Collaboration for a Sustainable Future Course, Coaching, Community</p>
    <div class="pill">Learn More <span class="go"><svg width="12" height="12" viewBox="0 0 12 12"><path d="M4 2l4 4-4 4" stroke="#23558f" stroke-width="2" fill="none"/></svg></span></div>
  </div>
</section>

<h2 class="sec-title" style="top:676px">Welcome To <span class="hl">VocaTerrana</span></h2>
<div class="divider" style="top:732px"></div>
<p class="lead" style="left:100px;top:784px;width:1000px;font-size:18px;line-height:30px">Lorem ipsum dolor sit amet, consectetur adipiscing elit. Donec semper venenatis dapibus. Ut pretium rutrum placerat. Nullam magna massa, suscipit id dui vel, iaculis facilisis purus</p>

<div class="feature" style="left:152px;top:876px">
  <span class="ic"><svg width="30" height="30" viewBox="0 0 30 30"><circle cx="15" cy="15" r="12" stroke="#2b2b2b" stroke-width="2.5" fill="none"/><circle cx="15" cy="15" r="6" stroke="#32b8a4" stroke-width="2.5" fill="none"/><circle cx="15" cy="15" r="2" fill="#2b2b2b"/></svg></span>
  <div><h3>Our <span>Mission</span></h3><p>Sed ut perspiciatis unde omnis iste natus error sit voluptatem accusantium.. <em>read more</em></p></div>
</div>
<div class="feature" style="left:598px;top:876px">
  <span class="ic"><svg width="32" height="28" viewBox="0 0 32 28"><circle cx="9" cy="8" r="4" fill="#32b8a4"/><circle cx="23" cy="8" r="4" fill="#2b2b2b"/><path d="M2 22a7 7 0 0 1 14 0z" fill="#32b8a4"/><path d="M16 22a7 7 0 0 1 14 0z" fill="#2b2b2b"/></svg></span>
  <div><h3>Our <span>Philosophy</span></h3><p>Sed ut perspiciatis unde omnis iste natus error sit voluptatem accusantium.. <em>read more</em></p></div>
</div>

<div class="service-band"></div>
<div class="service" style="left:100px">
  <div class="photo" role="img" aria-label="Graduates in caps and gowns" style="background:linear-gradient(180deg,#b9c6d2,#3d3f48)"><span class="badge"></span></div>
  <h4>Next Generation<br>Talent</h4>
  <div class="pill">Read More <span class="go"><svg width="12" height="12" viewBox="0 0 12 12"><path d="M4 2l4 4-4 4" stroke="#23558f" stroke-width="2" fill="none"/></svg></span></div>
</div>
<div class="service" style="left:355px">
  <div class="photo" role="img" aria-label="Students seated in a lecture hall" style="background:linear-gradient(180deg,#d8d3c8,#8a3a35)"><span class="badge"></span></div>
  <h4>Our<br>Courses</h4>
  <div class="pill">Read More <span class="go"><svg width="12" height="12" viewBox="0 0 12 12"><path d="M4 2l4 4-4 4" stroke="#23558f" stroke-width="2" fill="none"/></svg></span></div>
</div>
<div class="service" style="left:610px">
  <div class="photo" role="img" aria-label="Coach with a headset at a computer" style="background:linear-gradient(180deg,#e5eef4,#6b8fb3)"><span class="badge"></span></div>
  <h4>Online<br>Coaching</h4>
  <div class="pill">Read More <span class="go"><svg width="12" height="12" viewBox="0 0 12 12"><path d="M4 2l4 4-4 4" stroke="#23558f" stroke-width="2" fill="none"/></svg></span></div>
</div>
<div class="service" style="left:865px">
  <div class="photo" role="img" aria-label="Two people meeting at a desk" style="background:linear-gradient(180deg,#f2f2f2,#9fa9b4)"><span class="badge"></span></div>
  <h4>In-Person<br>Coaching</h4>
  <div class="pill">Read More <span class="go"><svg width="12" height="12" viewBox="0 0 12 12"><path d="M4 2l4 4-4 4" stroke="#23558f" stroke-width="2" fill="none"/></svg></span></div>
</div>

<section class="phases">
  <h2 class="sec-title" style="top:28px">Four Phase <span class="hl">Career Course</span></h2>
  <div class="divider" style="top:86px"></div>
  <p class="lead" style="left:120px;top:140px;width:960px;font-size:15.5px;line-height:26px">Through a proven four-phase process, integrating principles of lifelong learning, career transitions, entrepreneurship, change management, and innovation, our interdisciplinary, collaborative course is designed to guide you through creative change for career, lifestyle and/or next generation leadership.</p>

  <div class="phase" style="left:162px;top:258px"><h5>Clarify</h5><p>Duis autem vel eum iriure do<br>in hendrerit in vulputate.</p><div class="dot" style="background:var(--teal)"><svg width="10" height="10" viewBox="0 0 10 10"><path d="M3 1l4 4-4 4" stroke="#fff" stroke-width="2" fill="none"/></svg></div></div>
  <div class="phase" style="left:551px;top:258px"><h5>Collaborate</h5><p>Duis autem vel eum iriure do<br>in hendrerit in vulputate.</p><div class="dot" style="background:var(--teal)"><svg width="10" height="10" viewBox="0 0 10 10"><path d="M3 1l4 4-4 4" stroke="#fff" stroke-width="2" fill="none"/></svg></div></div>

  <svg class="abs" style="left:0;top:380px" width="1200" height="230" viewBox="0 0 1200 230">
    <defs><filter id="soft" x="-20%" y="-20%" width="140%" height="140%"><feDropShadow dx="0" dy="3" stdDeviation="5" flood-opacity=".18"/></filter></defs>
    <path d="M150 115H212A98 98 0 0 0 408 115" stroke="#32b8a4" stroke-width="30" fill="none"/>
    <path d="M408 115A98 98 0 0 1 604 115" stroke="#3176b5" stroke-width="30" fill="none"/>
    <path d="M604 115A98 98 0 0 0 800 115" stroke="#32b8a4" stroke-width="30" fill="none"/>
    <path d="M800 115A98 98 0 0 1 996 115H1040" stroke="#3176b5" stroke-width="30" fill="none"/>
    <g filter="url(#soft)" fill="#fff">
      <circle cx="310" cy="115" r="72"/><circle cx="506" cy="115" r="72"/><circle cx="702" cy="115" r="72"/><circle cx="898" cy="115" r="72"/>
    </g>
    <g fill="none" stroke-width="3" stroke-linecap="round">
      <circle cx="316" cy="98" r="14" stroke="#3176b5"/><path d="M310 112v6h12v-6M316 92v8" stroke="#3176b5"/>
      <circle cx="296" cy="128" r="6" stroke="#2b2b2b"/><path d="M284 146a12 12 0 0 1 24 0" stroke="#2b2b2b"/>
      <path d="M482 88h34a6 6 0 0 1 6 6v16a6 6 0 0 1-6 6h-20l-10 8v-8h-4a6 6 0 0 1-6-6V94a6 6 0 0 1 6-6z" stroke="#32b8a4"/>
      <path d="M500 120v4a6 6 0 0 0 6 6h14l10 8v-8a6 6 0 0 0 6-6v-16a6 6 0 0 0-6-6" stroke="#32b8a4"/>
      <circle cx="684" cy="96" r="7" stroke="#3176b5"/><circle cx="720" cy="96" r="7" stroke="#3176b5"/>
      <path d="M674 140v-22l10-10 18 10 18-10 10 10v22" stroke="#3176b5"/><path d="M702 118v22" stroke="#3176b5"/>
      <path d="M886 112a12 12 0 1 1 24 0c0 6-5 9-5 14h-14c0-5-5-8-5-14z" stroke="#32b8a4"/><path d="M892 132h12M894 138h8M898 84v-6M876 92l-4-4M920 92l4-4M868 112h-6M928 112h6" stroke="#32b8a4"/>
    </g>
  </svg>

  <div class="phase" style="left:355px;top:594px"><h5>Communicate</h5><p>Duis autem vel eum iriure do<br>in hendrerit in vulputate.</p><div class="dot" style="background:var(--navy)"><svg width="10" height="10" viewBox="0 0 10 10"><path d="M3 1l4 4-4 4" stroke="#fff" stroke-width="2" fill="none"/></svg></div></div>
  <div class="phase" style="left:745px;top:594px"><h5>Create</h5><p>Duis autem vel eum iriure do<br>in hendrerit in vulputate.</p><div class="dot" style="background:var(--navy)"><svg width="10" height="10" viewBox="0 0 10 10"><path d="M3 1l4 4-4 4" stroke="#fff" stroke-width="2" fill="none"/></svg></div></div>
</section>

<h2 class="sec-title" style="top:2120px">Our <span class="hl">Coaches</span></h2>
<div class="divider" style="top:2176px"></div>
<div class="coach-photo" role="img" aria-label="Portrait photo of coach Marion Adler Voss" style="left:104px;top:2248px;background:radial-gradient(circle at 50% 40%,#c9a97a,#3a2f26)"></div>
<div class="coach" style="left:335px;top:2282px">
  <h6>Marion Adler Voss</h6>
  <p>Certified Education, Career, Leadership Development Consultant with over 30 years experience in corporate, higher education, and NGO organizations, collaborating across disciplines and sectors.</p>
  <a>Read More »</a>
</div>
<div class="coach-photo" role="img" aria-label="Portrait photo of coach Delia Harwick" style="left:622px;top:2248px;background:radial-gradient(circle at 50% 40%,#b5a89a,#2a2a2a)"></div>
<div class="coach" style="left:862px;top:2282px">
  <h6>Delia Harwick</h6>
  <p>Delia Harwick is a connector, a communicator and a coach. She is the president and principal of Veltmark Executive Search and Career Advancement Services and is a Certified Master Coach, Executive Recruiter and Diversity Advocate</p>
  <a>Read More »</a>
</div>

<div class="gallery-bg"></div>
<h2 class="sec-title" style="top:2540px">View <span class="hl">Gallery</span></h2>
<div class="divider" style="top:2596px"></div>
<div class="tile" role="img" aria-label="Small green city skyline on a grassy globe" style="left:101px;top:2661px;width:362px;height:310px;background:linear-gradient(180deg,#e3eaee,#7fae4a)"><span>Sustainable Cities</span></div>
<div class="tile" role="img" aria-label="Hands holding a small plant in soil" style="left:468px;top:2661px;width:375px;height:150px;background:linear-gradient(180deg,#3c3a34,#6f8a46)"><span class="top">Equity Issues</span></div>
<div class="tile" role="img" aria-label="Group of hands holding seedlings together" style="left:468px;top:2819px;width:375px;height:152px;background:linear-gradient(180deg,#8aa05b,#4d5a30)"><span>Community</span></div>
<div class="tile" role="img" aria-label="Hands forming a frame around a tree" style="left:852px;top:2661px;width:250px;height:310px;background:linear-gradient(180deg,#6fb4e0,#e2c4a4 60%,#7aa943)"><span>Ecosystems</span></div>
<div class="tile" role="img" aria-label="Person working beside solar panels in a garden" style="left:101px;top:2980px;width:552px;height:209px;background:linear-gradient(90deg,#34475d,#6c8a55 60%,#a9b88a)"><span>Education</span></div>
<div class="tile" role="img" aria-label="Wind turbine and solar panels under a blue sky" style="left:661px;top:2980px;width:441px;height:209px;background:linear-gradient(180deg,#3f7fc4,#a9cbe8 55%,#2f4e78)"><span>Technology</span></div>

<div class="blog-bg"></div>
<h2 class="sec-title" style="top:3272px">Rising over <span class="hl">the Rift</span></h2>
<div class="divider" style="top:3328px"></div>
<svg class="side-arrow" style="left:62px" width="18" height="36" viewBox="0 0 18 36"><path d="M15 3 3 18l12 15" stroke="#555" stroke-width="2.5" fill="none"/></svg>
<svg class="side-arrow" style="left:1120px" width="18" height="36" viewBox="0 0 18 36"><path d="M3 3l12 15L3 33" stroke="#555" stroke-width="2.5" fill="none"/></svg>
<article class="post" style="left:101px">
  <div class="photo" role="img" aria-label="Puzzle pieces with coaching words and a hand placing a piece" style="background:linear-gradient(135deg,#e8e8e8,#9db6d6 60%,#3a6aa8)"><div class="date">23<small>JUN</small></div></div>
  <h4>Sed ut perspiciatis unde iste mo</h4>
  <p>Duis autem vel eum iriure dolor in hendrerit ink vulput ate velit esse molestie facilisis.</p>
  <a>Read More »</a>
</article>
<article class="post" style="left:444px">
  <div class="photo" role="img" aria-label="Chalkboard with career development words written on it" style="background:linear-gradient(135deg,#2f3a3d,#4d5a5e)"><div class="date">23<small>JUN</small></div></div>
  <h4>Sed ut perspiciatis unde iste mo</h4>
  <p>Duis autem vel eum iriure dolor in hendrerit ink vulput ate velit esse molestie facilisis.</p>
  <a>Read More »</a>
</article>
<article class="post" style="left:786px">
  <div class="photo" role="img" aria-label="Diagram of career factors with a person thinking" style="background:linear-gradient(90deg,#ffffff,#f0eeee 70%,#d9c7b8)"><div class="date">23<small>JUN</small></div></div>
  <h4>Sed ut perspiciatis unde iste mo</h4>
  <p>Duis autem vel eum iriure dolor in hendrerit ink vulput ate velit esse molestie facilisis.</p>
  <a>Read More »</a>
</article>

<svg class="footer-curve" width="1200" height="60" viewBox="0 0 1200 60" preserveAspectRatio="none"><path d="M0 60Q600 -20 1200 60z" fill="#2c2c2c"/></svg>
<footer class="site-footer"></footer>
<div class="footer-badge"></div>
<div class="fcol" style="left:101px">
  <h5>Quick Links</h5>
  <ul><li>Home</li><li>About</li><li>Services</li><li>Blog</li><li>Contact</li></ul>
</div>
<div class="fcol" style="left:272px">
  <h5>Contact Details</h5>
  <div>VocaTerrana</div>
  <div style="margin-top:6px;font-size:11.5px;line-height:16px">123, Ut wisi enim ad minim veniam,<br>Mor nostrud lation - 123456</div>
  <div class="line"><svg width="12" height="12" viewBox="0 0 24 24"><path fill="#ddd" d="M6.6 10.8a15 15 0 0 0 6.6 6.6l2.2-2.2a1 1 0 0 1 1-.25 11.4 11.4 0 0 0 3.6.6 1 1 0 0 1 1 1V20a1 1 0 0 1-1 1A17 17 0 0 1 3 4a1 1 0 0 1 1-1h3.5a1 1 0 0 1 1 1c0 1.25.2 2.45.6 3.6a1 1 0 0 1-.25 1z"/></svg>555-014-2390</div>
  <div class="line"><svg width="12" height="12" viewBox="0 0 12 12"><rect x="1" y="4" width="10" height="7" fill="#ddd"/><rect x="3" y="1" width="6" height="3" fill="#ddd"/></svg>555-014-2390</div>
  <div class="line"><svg width="12" height="10" viewBox="0 0 12 10"><rect x=".5" y=".5" width="11" height="9" fill="none" stroke="#ddd"/><path d="M1 1l5 4 5-4" stroke="#ddd" fill="none"/></svg>info@vocaterrana.com</div>
</div>
<div class="fcol" style="left:525px">
  <h5>Quick Inquiry</h5>
  <div class="field">Name</div>
  <div class="field">Email</div>
  <div class="field msg">Message</div>
  <div class="submit">Submit</div>
</div>
<div class="fcol" style="left:816px">
  <h5>View Feeds</h5>
  <div class="feed-head">GREEN PATH JOBS<small>view more connections</small></div>
  <ul class="feed">
    <li>Education Development Coordinator<small>Civic Canopy Council</small></li>
    <li>Environmental Communications Specialist<small>Northfield Analytics Group, Inc.</small></li>
    <li>Sales Coordinator<small>Reworth, Inc.</small></li>
  </ul>
</div>
<div class="copyright">Copyright © 2016 VocaTerrana. All Rights Reserved.</div>

</div>
</body>
</html>
```